Web Design Project for a Software & Consulting Company

We have just completed a recent ArtHerdly project for a new logo (see attached).
As the next stage of our rebranding we now require a website re-design to complement the new logo.
Our current site, http://www.corvinsoft.example was built in-house and does not come across as professional as we would like. We supply software and associated services to some of the world’s largest oil companies and we need our site to reflect that level of client.
We will also be posting another design project for brochures, PowerPoint slides and other materials very soon.
We would like designs for…
Home page
Product page
• TZQ
• BLV
• PNJ
Services
News page
About Us page
Contact Us page
Page for mobile devices that gives basic company and product information
Currently the site is small but we intend to increase content to include white papers etc. this should be taken into account when designing the navigation therefore we would prefer navigation through styled text links rather than images.
Colour schemes should broadly be taken from our new logo, where the dark blue and dark green from the left and right sides of the logo are the main colours, but other, brighter accent colours can be used to highlight sections or content.
Dark Blue = C:88, M:55, Y:44, K:28
Dark Green = C:87, M:53, Y:50, K:50
NB: Don’t use the logo on our current site, make sure you use the one attached.
We would prefer the final file format to be a layered PSD.
The site should be clean and professional and communicate the following...
• That we have a great depth and breadth of knowledge about our customers’ business, enabling us to deliver the best systems and solutions.
• That we are a leading provider of cost estimation and control solutions to the oil and gas industry.
• The benefits of our software and consulting services.
• Show that we deliver outstanding customer service and value with a very high level of professionalism
• The site should have no Flash and be able to self-adjust to fit any screen size.
Things to avoid …
• Obvious and clichéd oil industry imagery, no oil rigs
• Cartoon style graphics
Our Background
We are an integrated software and consulting organization specialising in the drilling side of the oil and gas industry. Simply put our software helps companies better understand, predict and communicate the cost of drilling wells.
We have 3 software products and a consulting offering consisting of…
• TZQ - Probabilistic time and cost software
• BLV – Cost tracking and reporting software
• PNJ – (currently known as DrillSavant) – Lessons learned software
• Consulting services
Our systems are in use in over 30 countries with a broad range of clients including: GN, Marovel, Dunt, Koruna, VELO Sirkami, FALUMI and Quintex.
Our current site can be found at www.corvinsoft.example
Our main competitors are
• http://www.drovanic.example/
• http://www.sumbrask.example/
• http://www.kve.example/services/software-solutions/p1-
Our depth of drilling knowledge, quality of software and collaboration with clients differentiate us form the competition.
We strive for very high levels of customer service.
We look forward to receiving your designs!
Updates
Thanks to all the designers who have submitted a design, we appreciate the effort.
We will do our best to give individual feedback on each design but given that many are quite similar we thought we would give some general feedback first.
Nearly all the designs submitted so far have been slight variations on…
-
Top Menu
-
Scrolling Photo Banner
-
4 Columns
-
Body
-
Deep Footer
These designs are well executed but they are basically the same layout as our existing site and while there is nothing inherently wrong with this layout we would like to see some designs that are a bit more innovative and different. We don’t really want just a polished version of our current site.
Thanks again,
CVS
Thanks to everyone who has submitted a design, the response has been great.
We are close to making a decision so if you are intending to submit a design please do it soon, the deadline is only a few days away.
Thanks again.
CVS
Target Market(s)
Mid to high level executives
Industry/Entity Type
Oil And Gas
Look and feel

```html
<!DOCTYPE html>
<html lang="fr">
<head>
<meta charset="utf-8">
<title>Corvin Soft — News</title>
<link href="https://fonts.googleapis.com/css2?family=Ubuntu:wght@400;500&family=PT+Sans+Narrow&family=Arimo:ital@0;1&display=swap" rel="stylesheet">
<style>
:root{
  --teal:#1f5567;
  --ink:#2a2a2a;
  --body:#4a4a4a;
  --rule:#c9c9c9;
  --link:#2d4f7a;
  --white:#fff;
  --footer-text:#e8f0f2;
  --footer-rule:#5c8794;
}
*{margin:0;padding:0;box-sizing:border-box}
html,body{width:843px;height:1200px;overflow:hidden;background:var(--white)}
body{position:relative;font-family:"Arimo",Arial,sans-serif;color:var(--body)}
h1,h2,h3{font-weight:400}
.abs{position:absolute}

.brand{left:104px;top:32px;display:flex;align-items:center;gap:8px}
.brand-mark{width:22px;height:22px;border-radius:50%;background:var(--teal)}
.brand-name{font-family:"Ubuntu",sans-serif;font-weight:500;font-size:22px;color:var(--teal);letter-spacing:.5px}

.main-nav{left:366px;top:49px;display:flex;font-family:"PT Sans Narrow",sans-serif;font-size:12px;color:#111}
.main-nav a{color:inherit;text-decoration:none;height:22px;line-height:22px;padding:0 10px;margin-right:12px;border-radius:3px}
.main-nav a.is-current{background:var(--teal);color:var(--white);border:1px solid #0f3340}
.main-nav a:last-child{margin-right:0}

.hero{left:84px;top:114px;width:677px;height:212px;overflow:hidden;
  background:radial-gradient(ellipse at 50% 40%,#dbe7ee 0%,#9fbccd 45%,#416e8a 80%,#1e3d58 100%)}
.hero-band{left:0;top:146px;width:100%;height:46px;background:rgba(21,70,86,.92)}
.hero-title{left:24px;top:157px;font-family:"Ubuntu",sans-serif;font-weight:500;font-size:19px;color:var(--white)}

.news-item{left:84px;width:677px}
.news-thumb{left:0;top:0;width:81px;height:60px}
.news-title{left:98px;top:-4px;font-family:"Ubuntu",sans-serif;font-size:17px;color:var(--teal);white-space:nowrap}
.news-text{left:98px;top:27px;width:575px;font-size:8.9px;line-height:12px;color:var(--body)}
.read-more{right:8px;font-style:italic;font-size:9px;color:var(--link);text-decoration:underline}
.divider{left:85px;width:676px;height:1px;background:var(--rule)}

.site-footer{left:84px;top:998px;width:677px;height:202px;background:var(--teal);color:var(--footer-text)}
.col-head{font-family:"PT Sans Narrow",sans-serif;font-size:12px;color:var(--white);padding-bottom:4px;border-bottom:1px solid var(--footer-rule)}
.address{font-size:8.6px;line-height:12px;margin-top:6px;white-space:nowrap}
.badge{width:118px;height:40px}
.touch-head{font-family:"Ubuntu",sans-serif;font-size:14px;color:var(--white);width:140px;padding-bottom:5px;
  border-bottom:2px solid transparent;border-image:linear-gradient(90deg,#3aa6c6,transparent) 1}
.field{width:141px;height:19px;background:var(--white);border:1px solid #9bb;border-radius:2px;font-size:9px;color:#333;padding:3px 7px}
.field.message{height:45px}
.submit-btn{width:46px;height:16px;background:linear-gradient(#fff,#dcdcdc);border:1px solid #999;border-radius:2px;font-size:7.5px;color:#222;text-align:center;line-height:14px}
.footer-blurb{left:19px;top:117px;width:472px;font-size:8.4px;line-height:10.4px}
.blurb-rule{left:19px;top:108px;width:470px;height:1px;background:var(--footer-rule)}
.legal-rule{left:0;top:177px;width:677px;height:1px;background:#2f6678}
.legal{top:188px;font-size:7.6px;color:var(--white)}
</style>
</head>
<body>

<header>
  <div class="abs brand"><span class="brand-mark"></span><span class="brand-name">CORVIN SOFT</span></div>
  <nav class="abs main-nav">
    <a href="#">HOME</a><a href="#">PRODUCTS</a><a href="#">SERVICES</a><a href="#" class="is-current">NEWS</a><a href="#">ABOUT US</a><a href="#">CONTACT US</a>
  </nav>
</header>

<section class="abs hero" role="img" aria-label="Close-up photograph of newspaper pages with the large printed word News">
  <div class="abs hero-band"></div>
  <h1 class="abs hero-title">News</h1>
</section>

<main>
  <article class="abs news-item" style="top:365px;height:110px">
    <div class="abs news-thumb" role="img" aria-label="Photo of a man examining a laptop with a magnifying glass" style="background:linear-gradient(135deg,#8fa3b3,#3f5466)"></div>
    <h2 class="abs news-title">On sait depuis longtemps que travailler</h2>
    <p class="abs news-text">Le Lorem Ipsum est simplement du faux texte employé dans la composition et la mise en page avant impression. Le Lorem Ipsum est le faux texte standard de l'imprimerie depuis les années 1500, quand un peintre anonyme assembla ensemble des morceaux de texte pour réaliser un livre spécimen de polices de texte Il n'a pas fait que survivre cinq siècles, mais s'est aussi adapté à la bureautique informatique, sans que son contenu n'en soit modifié. Il a été popularisé dans les années 1960 grâce à la vente de feuilles Tracefeuil contenant des passages du Lorem Ipsum, et, plus récemment, par son inclusion dans des applications de mise en page de texte, comme Orvale PageSet</p>
    <a class="abs read-more" href="#" style="top:98px">Read More</a>
  </article>
  <div class="abs divider" style="top:484px"></div>

  <article class="abs news-item" style="top:522px;height:110px">
    <div class="abs news-thumb" role="img" aria-label="Photo of a man typing at a keyboard" style="background:linear-gradient(135deg,#b6c2cc,#4a5d6e)"></div>
    <h2 class="abs news-title">Du sens est source de distractions</h2>
    <p class="abs news-text">Le Lorem Ipsum est simplement du faux texte employé dans la composition et la mise en page avant impression. Le Lorem Ipsum est le faux texte standard de l'imprimerie depuis les années 1500, quand un peintre anonyme assembla ensemble des morceaux de texte pour réaliser un livre spécimen de polices de texte Il n'a pas fait que survivre cinq siècles, mais s'est aussi adapté à la bureautique informatique, sans que son contenu n'en soit modifié. Il a été popularisé dans les années 1960 grâce à la vente de feuilles Tracefeuil contenant des passages du Lorem Ipsum, et, plus récemment, par son inclusion dans des applications de mise en page de texte, comme Orvale PageSet</p>
    <a class="abs read-more" href="#" style="top:95px">Read More</a>
  </article>
  <div class="abs divider" style="top:642px"></div>

  <article class="abs news-item" style="top:680px;height:110px">
    <div class="abs news-thumb" role="img" aria-label="Photo of a businesswoman touching virtual interface icons" style="background:linear-gradient(135deg,#6b7c8a,#1e2c3a)"></div>
    <h2 class="abs news-title">Plusieurs variations de Lorem Ipsum peuvent</h2>
    <p class="abs news-text">Le Lorem Ipsum est simplement du faux texte employé dans la composition et la mise en page avant impression. Le Lorem Ipsum est le faux texte standard de l'imprimerie depuis les années 1500, quand un peintre anonyme assembla ensemble des morceaux de texte pour réaliser un livre spécimen de polices de texte Il n'a pas fait que survivre cinq siècles, mais s'est aussi adapté à la bureautique informatique, sans que son contenu n'en soit modifié. Il a été popularisé dans les années 1960 grâce à la vente de feuilles Tracefeuil contenant des passages du Lorem Ipsum, et, plus récemment, par son inclusion dans des applications de mise en page de texte, comme Orvale PageSet</p>
    <a class="abs read-more" href="#" style="top:96px">Read More</a>
  </article>
  <div class="abs divider" style="top:809px"></div>

  <article class="abs news-item" style="top:858px;height:110px">
    <div class="abs news-thumb" role="img" aria-label="Photo of a businessman with chalk-written technology words" style="background:linear-gradient(135deg,#2c4a66,#0d1a28)"></div>
    <h2 class="abs news-title">Contrairement à une opinion répandue</h2>
    <p class="abs news-text">Le Lorem Ipsum est simplement du faux texte employé dans la composition et la mise en page avant impression. Le Lorem Ipsum est le faux texte standard de l'imprimerie depuis les années 1500, quand un peintre anonyme assembla ensemble des morceaux de texte pour réaliser un livre spécimen de polices de texte Il n'a pas fait que survivre cinq siècles, mais s'est aussi adapté à la bureautique informatique, sans que son contenu n'en soit modifié. Il a été popularisé dans les années 1960 grâce à la vente de feuilles Tracefeuil contenant des passages du Lorem Ipsum, et, plus récemment, par son inclusion dans des applications de mise en page de texte, comme Orvale PageSet</p>
    <a class="abs read-more" href="#" style="top:98px">Read More</a>
  </article>
</main>

<footer class="abs site-footer">
  <div class="abs" style="left:21px;top:18px;width:104px">
    <h3 class="col-head">EUROPE</h3>
    <p class="address">18 Harlow Row<br>Dunmere, DN4 2QT<br>Phone:+44(0)1632 960418<br>Email:eu@corvinsoft.example</p>
  </div>
  <div class="abs" style="left:162px;top:17px;width:104px">
    <h3 class="col-head">NORTH AMERICA</h3>
    <p class="address">4100 Calder Park Dr, Suite 210<br>Linwood, TX 77590<br>Phone:(555) 014 3372<br>Email:us@corvinsoft.example</p>
  </div>
  <div class="abs" style="left:319px;top:17px;width:158px">
    <h3 class="col-head">OUR GOLD BUSINESS PARTNER</h3>
    <div class="badge" style="margin:10px 0 0 18px;background:#2d6577;border-radius:4px"></div>
  </div>
  <div class="abs blurb-rule"></div>
  <p class="abs footer-blurb">Lorem ipsum dolor sit amet, consectetur adipiscing elit. Donec semper nisl eget ante vehicula at viverra est porta. Morbi eleifend, turpis eget vehicula porta, leo velit facilisis justo, quis vehicula velit erat nec est. Pellentesque habitant morbi tristique senectus et netus et malesuada fames ac turpis egestas. Pellentesque consequat est vel metus luctus commodo. In hac habitasse platea dictumst. Suspendisse justo ipsum,</p>

  <div class="abs" style="left:513px;top:12px">
    <h3 class="touch-head">Get in touch</h3>
  </div>
  <div class="abs field" style="left:513px;top:45px">Name</div>
  <div class="abs field" style="left:513px;top:70px">E-mail</div>
  <div class="abs field message" style="left:513px;top:95px">Message</div>
  <div class="abs submit-btn" style="left:608px;top:146px">SUBMIT</div>

  <div class="abs legal-rule"></div>
  <p class="abs legal" style="left:19px">Privacy Policy &nbsp;|&nbsp; Terms &amp; Conditions</p>
  <p class="abs legal" style="right:22px">© Copyrights 2012 Corvin Soft</p>
</footer>

</body>
</html>
```